Locksmith Business Cards

My father-in-law is in need of new business cards for his locksmith business and I need to impress him. Kindly help me out!

You can see the previous business card attached. It is a family run business in North Wales.

No individual names on the cards.

Key Things to Feature:
- The words "Prompt", "Local", "Reliable" (as you can see under the logo on the website)
- 24h Emergency Service
- Covering All of North Wales, the Wirral and Chester
- The color blue
- A key or a lock would be interesting (similar to the ones that come up when you google locksmith business card)

Optional (only if design includes bullet points, like the example below):
https://imgvaultcdn.net/samples/208314/55172/55172_3904821_208314_image.jpg
- Residential / Commercial / Automotive
- Alarms & Cameras
- Key Cutting & Safes

https://www.brynhafod-locksmiths.co.uk/

Industry/Entity Type

Locksmith

Contact Information for Business Card

01632 960 418
07700 900 362
brynhafodlocksmiths@mailvane.com
Brynhafod Locksmiths, The Willow Barn, 7 Tannery Rd., Llandudno LL99 4QX
www.brynhafod-locksmiths.co.uk

Requirements
Must have
• - The words "Prompt", "Local", "Reliable" (as you can see under the logo on the website)
• - 24h Emergency Service
• - Covering All of North Wales, the Wirral and Chester
Nice to have
• - A key or a lock would be interesting (similar to the ones that come up when you google locksmith business card)

```html
<!DOCTYPE html>
<html lang="en">
<head>
<meta charset="UTF-8">
<title>Brynhafod Locksmiths – Business Card</title>
<link href="https://fonts.googleapis.com/css2?family=Roboto+Condensed:wght@400;700&family=Roboto:wght@400;500&display=swap" rel="stylesheet">
<style>
  :root {
    --navy: #232a63;
    --accent: #3d55b0;
    --ink: #1f2557;
    --white: #ffffff;
    --muted: #c9cff0;
    --stage: #e9eaef;
    --rule: #5a6fc0;
  }
  * { box-sizing: border-box; margin: 0; padding: 0; }
  html, body {
    width: 1200px; height: 900px; overflow: hidden;
    background: var(--stage);
    font-family: "Roboto", sans-serif;
  }
  .sheet {
    position: relative; width: 1200px; height: 900px;
    display: flex; flex-direction: column; align-items: center;
    justify-content: center; gap: 50px;
  }
  .card {
    position: relative; width: 600px; height: 375px;
    border-radius: 22px; overflow: hidden;
    box-shadow: 0 8px 24px rgba(20, 24, 60, 0.18);
  }

  /* Front */
  .card--front { background: var(--white); color: var(--ink); }
  .brand { position: absolute; display: flex; align-items: center; gap: 14px; }
  .brand__mark { width: 46px; height: 46px; border-radius: 8px; flex: none; }
  .brand__name {
    font-family: "Roboto Condensed", sans-serif; font-weight: 700;
    text-transform: uppercase; line-height: 0.95; letter-spacing: 0.5px;
  }
  .card--front .brand { left: 44px; top: 36px; }
  .card--front .brand__mark { background: var(--navy); }
  .card--front .brand__name { color: var(--navy); font-size: 34px; }
  .tagline {
    position: absolute; left: 104px; top: 116px;
    font-family: "Roboto Condensed", sans-serif; font-size: 17px; color: var(--ink);
  }
  .divider {
    position: absolute; left: 30px; right: 30px; top: 190px;
    height: 1.5px; background: var(--rule);
  }
  .contacts { position: absolute; left: 40px; top: 212px; list-style: none; }
  .contacts li {
    display: flex; align-items: center; gap: 9px;
    font-size: 13.5px; line-height: 25px; color: var(--ink);
  }
  .contacts svg { width: 13px; height: 13px; fill: var(--navy); flex: none; }
  .address {
    position: absolute; right: 40px; bottom: 36px; text-align: right;
    font-style: normal;
    font-family: "Roboto Condensed", sans-serif; font-size: 15px; line-height: 20px; color: var(--ink);
  }
  .address__company { color: var(--accent); }

  /* Back */
  .card--back { background: var(--navy); color: var(--white); }
  .card--back .brand { left: 44px; top: 34px; }
  .card--back .brand__mark { background: var(--white); }
  .card--back .brand__name { color: var(--white); font-size: 38px; }
  .service-title {
    position: absolute; left: 44px; top: 124px;
    font-family: "Roboto Condensed", sans-serif; font-size: 27px; letter-spacing: 0.5px;
  }
  .services { position: absolute; left: 62px; top: 166px; list-style: none; }
  .services li {
    position: relative; padding-left: 22px;
    font-family: "Roboto Condensed", sans-serif; font-size: 20px; line-height: 29px;
  }
  .services li::before {
    content: ""; position: absolute; left: 0; top: 10px;
    width: 9px; height: 9px; border-radius: 50%; background: var(--white);
  }
  .coverage {
    position: absolute; left: 44px; right: 44px; bottom: 24px;
    font-family: "Roboto Condensed", sans-serif; font-size: 16px; color: var(--muted);
    letter-spacing: 0.3px;
  }
</style>
</head>
<body>
<main class="sheet">

  <section class="card card--front" aria-label="Business card front">
    <div class="brand">
      <span class="brand__mark"></span>
      <span class="brand__name">Brynhafod<br>Locksmiths</span>
    </div>
    <p class="tagline">Prompt. Local. Reliable</p>
    <div class="divider"></div>

    <ul class="contacts">
      <li>
        <svg viewBox="0 0 24 24"><path d="M6.6 10.8a15.1 15.1 0 0 0 6.6 6.6l2.2-2.2a1 1 0 0 1 1-.25 11.4 11.4 0 0 0 3.6.57 1 1 0 0 1 1 1V20a1 1 0 0 1-1 1A17 17 0 0 1 3 4a1 1 0 0 1 1-1h3.5a1 1 0 0 1 1 1c0 1.25.2 2.45.57 3.6a1 1 0 0 1-.25 1z"/></svg>
        01632 960 418
      </li>
      <li>
        <svg viewBox="0 0 24 24"><path d="M7 1h10a2 2 0 0 1 2 2v18a2 2 0 0 1-2 2H7a2 2 0 0 1-2-2V3a2 2 0 0 1 2-2zm0 4v13h10V5zm5 14.5a1.2 1.2 0 1 0 0 2.4 1.2 1.2 0 0 0 0-2.4z"/></svg>
        07700 900 362
      </li>
      <li>
        <svg viewBox="0 0 24 24"><path d="M2 5h20v14H2zm2 2v.5l8 5 8-5V7zm0 2.8V17h16V9.8l-8 5z"/></svg>
        brynhafodlocksmiths@mailvane.com
      </li>
      <li>
        <svg viewBox="0 0 24 24"><path d="M12 2a10 10 0 1 0 0 20 10 10 0 0 0 0-20zm6.9 6h-2.9a15 15 0 0 0-1.4-3.6A8 8 0 0 1 18.9 8zM12 4c.8 1.1 1.5 2.5 1.9 4h-3.8c.4-1.5 1.1-2.9 1.9-4zM4.3 14a8 8 0 0 1 0-4h3.4a16 16 0 0 0 0 4zm.8 2H8a15 15 0 0 0 1.4 3.6A8 8 0 0 1 5.1 16zM8 8H5.1a8 8 0 0 1 4.3-3.6A15 15 0 0 0 8 8zm4 12c-.8-1.1-1.5-2.5-1.9-4h3.8c-.4 1.5-1.1 2.9-1.9 4zm2.3-6H9.7a14 14 0 0 1 0-4h4.6a14 14 0 0 1 0 4zm.3 5.6A15 15 0 0 0 16 16h2.9a8 8 0 0 1-4.3 3.6zm1.7-5.6a16 16 0 0 0 0-4h3.4a8 8 0 0 1 0 4z"/></svg>
        www.brynhafod-locksmiths.co.uk
      </li>
    </ul>

    <address class="address">
      <span class="address__company">Brynhafod Locksmiths,</span><br>
      The Willow Barn, 7 Tannery Rd.,<br>
      Llandudno LL99 4QX
    </address>
  </section>

  <section class="card card--back" aria-label="Business card back">
    <div class="brand">
      <span class="brand__mark"></span>
      <span class="brand__name">Brynhafod<br>Locksmiths</span>
    </div>
    <p class="service-title">24h Emergency Service</p>
    <ul class="services">
      <li>Residential</li>
      <li>Commercial</li>
      <li>Automotive</li>
      <li>Alarms &amp; Cameras</li>
      <li>Key Cutting &amp; Safes</li>
    </ul>
    <p class="coverage">Covering All of North Wales, the Wirral and Chester</p>
  </section>

</main>
</body>
</html>
```